Stylish Business Cards Wanted

- DOUBLE SIDED Design Required -

High end, edgy cards for a corporate and personal stylist. Must include logo,
Name: Belinda Harwick
Title: Director and Stylist
telephone : +61 8 7142 5809
email: belinda@theloombriefing.example
website: theloombriefing.example
Tag: Corporate Workwear & Uniform Specialist | Personal Stylist
Would like nice icons for telephone, email, website

Target Market(s)

Businesses wanting stylish uniforms, people wanting stylish wardrobes

Industry/Entity Type

Corporate Workwear Stylist

Contact Information for Business Card

I would like black, white and gold foiling incorporated in the design - possibly a touch of the other colours on my branding guide attached Name: Belinda Harwick Title: Director and Stylist telephone : +61 8 7142 5809 email: belinda@theloombriefing.example website: theloombriefing.example Tag: Corporate Workwear & Uniform Specialist | Personal Stylist Would like nice icons for telephone, email, website

Font styles to use
Other font styles liked:
• Raleway

Colors

Designer to choose colors to be used in the design.

Requirements
Must have
• Gold foil accents

```html
<!DOCTYPE html>
<html lang="en">
<head>
<meta charset="utf-8">
<title>The Loom Briefing — Business Cards</title>
<link rel="stylesheet" href="https://fonts.googleapis.com/css2?family=Montserrat:wght@600&family=Roboto:wght@400&family=Yellowtail&family=Kalam:wght@400&display=swap">
<style>
  :root {
    --navy: #141b30;
    --gold: #dcb552;
    --paper: #fbfbfa;
    --ink: #1b2036;
    --backdrop: #c9c9c9;
    --accent-pink: #d8436f;
  }
  * { margin: 0; padding: 0; box-sizing: border-box; }
  html, body { width: 1200px; height: 852px; overflow: hidden; }
  body { background: var(--backdrop); position: relative; font-family: "Roboto", Arial, sans-serif; }

  .card {
    position: absolute;
    width: 500px;
    height: 286px;
    border-radius: 18px;
    overflow: hidden;
    box-shadow: 0 6px 18px rgba(0,0,0,0.18);
  }

  /* Back side */
  .card--back { left: 90px; top: 190px; background: var(--navy); }
  .card--back .brand {
    position: absolute; left: 0; right: 0; top: 50%;
    transform: translateY(-50%);
    text-align: center;
    font-family: "Montserrat", Arial, sans-serif;
    font-weight: 600;
    font-size: 36px;
    letter-spacing: 1px;
    color: var(--gold);
  }

  /* Front side */
  .card--front { left: 610px; top: 376px; background: var(--paper); }

  .band { position: absolute; left: 0; top: 0; width: 500px; height: 286px; }

  .front__brand {
    position: absolute; left: 30px; top: 112px;
    width: 210px;
    font-family: "Montserrat", Arial, sans-serif;
    font-weight: 600;
    font-size: 20px;
    line-height: 1.2;
    color: var(--navy);
    letter-spacing: 0.3px;
  }

  .tagline {
    position: absolute; right: 32px; top: 22px;
    text-align: right;
    font-family: "Kalam", cursive;
    font-size: 14px;
    line-height: 1.3;
    color: var(--ink);
  }
  .tagline .mark { color: var(--accent-pink); font-size: 11px; margin-left: 3px; }

  .contact {
    position: absolute; left: 266px; top: 102px;
    list-style: none;
    font-size: 12.5px;
    color: var(--ink);
  }
  .contact li { display: flex; align-items: center; gap: 8px; height: 20px; white-space: nowrap; }
  .contact svg { width: 13px; height: 13px; flex: none; }

  .social {
    position: absolute; left: 272px; top: 199px;
    display: flex; align-items: center; gap: 8px;
    font-size: 12.5px; line-height: 1; color: var(--navy);
  }
  .social__square { width: 11px; height: 11px; background: var(--navy); border-radius: 2px; }

  .person { position: absolute; left: 30px; top: 204px; }
  .person__name {
    font-family: "Yellowtail", cursive;
    font-size: 26px;
    color: var(--gold);
    line-height: 1.05;
  }
  .person__title { font-size: 12.5px; color: var(--ink); margin-top: 3px; }
</style>
</head>
<body>

  <section class="card card--back" aria-label="Card back">
    <div class="brand">The Loom Briefing</div>
  </section>

  <section class="card card--front" aria-label="Card front">
    <svg class="band" viewBox="0 0 500 286" aria-hidden="true">
      <path d="M0 264 L188 264 L236 236 L500 236 L500 286 L0 286 Z" fill="var(--navy)"/>
      <path d="M240 236 Q236 184 268 182 L500 182 L500 270 Q500 286 484 286 L240 286 Z" fill="var(--gold)"/>
    </svg>

    <div class="front__brand">The Loom Briefing</div>

    <div class="tagline">
      <div>Corporate Workwear<span class="mark">&#10077;</span></div>
      <div>&amp; Uniform Specialist<span class="mark">&#10077;</span></div>
      <div>Personal Stylist<span class="mark">&#10077;</span></div>
    </div>

    <ul class="contact">
      <li>
        <svg viewBox="0 0 16 16"><circle cx="8" cy="8" r="7.2" fill="none" stroke="var(--gold)" stroke-width="1.4"/><path d="M5.2 4.6c.4-.4 1-.3 1.2.2l.5 1.1c.1.3 0 .6-.2.8l-.4.4c.4.9 1.1 1.6 2 2l.4-.4c.2-.2.5-.3.8-.2l1.1.5c.5.2.6.8.2 1.2l-.5.5c-2.2.4-5.6-3-5.6-5.6z" fill="var(--gold)"/></svg>
        +61 8 7142 5809
      </li>
      <li>
        <svg viewBox="0 0 16 16"><rect x="1.5" y="3.5" width="13" height="9" rx="1" fill="none" stroke="var(--gold)" stroke-width="1.4"/><path d="M2 4l6 5 6-5" fill="none" stroke="var(--gold)" stroke-width="1.4"/></svg>
        belinda@theloombriefing.example
      </li>
      <li>
        <svg viewBox="0 0 16 16"><circle cx="8" cy="8" r="6.5" fill="none" stroke="var(--gold)" stroke-width="1.4"/><ellipse cx="8" cy="8" rx="2.8" ry="6.5" fill="none" stroke="var(--gold)" stroke-width="1.2"/><path d="M1.5 8h13" stroke="var(--gold)" stroke-width="1.2"/></svg>
        www.theloombriefing.example
      </li>
    </ul>

    <div class="social">
      <span class="social__square"></span>
      <span>/theloombriefing101</span>
    </div>

    <div class="person">
      <div class="person__name">Belinda Harwick</div>
      <div class="person__title">Director and Stylist</div>
    </div>
  </section>

</body>
</html>
```